Upmarket Dessert Lounge needs a Business Card Design

We are an upmarket dessert lounge needing a business card to match our image.

We want something that is simple yet beautiful, feminine, classy, sophisticated and elegant. We want it to stand out and don't mind if it is bold.

The design should include our logo and colours of red or maroon with gold highlights. We don't mind if black is used.

Marlow & Quince

Target Market(s)

For those who like to indulge or treat themselves and give in to their temptations on good quality desserts.

Industry/Entity Type

Business

Requirements
Must have
• Must include our logo and our name

Marlow & Quince

M & Q

```html
<!DOCTYPE html>
<html lang="en">
<head>
<meta charset="utf-8">
<title>Marlow &amp; Quince – Business Card</title>
<link rel="stylesheet" href="https://fonts.googleapis.com/css2?family=Open+Sans:wght@400;600;700&display=swap">
<style>
  :root {
    --backdrop: #d9d9d9;
    --card-black: #000000;
    --maroon: #7a1416;
    --gold: #fbd095;
    --gold-deep: #f2c27e;
    --white: #ffffff;
  }
  * { margin: 0; padding: 0; box-sizing: border-box; }
  html, body {
    width: 956px;
    height: 1200px;
    overflow: hidden;
    background: var(--backdrop);
    font-family: "Open Sans", Arial, sans-serif;
  }
  .canvas {
    position: relative;
    width: 956px;
    height: 1200px;
  }
  .card {
    position: absolute;
    width: 798px;
    height: 457px;
    border-radius: 30px;
    background: var(--card-black);
    overflow: hidden;
  }
  .card--front { left: 79px; top: 70px; }
  .card--back  { left: 74px; top: 632px; }

  .card__wave {
    position: absolute;
    inset: 0;
    width: 100%;
    height: 100%;
  }
  .wordmark {
    position: absolute;
    color: var(--gold);
    font-weight: 600;
    white-space: nowrap;
  }
  .wordmark--front {
    left: 52px;
    top: 146px;
    width: 330px;
    text-align: center;
    font-size: 31px;
  }
  .wordmark--back {
    left: 0;
    width: 100%;
    top: 160px;
    text-align: center;
    font-size: 104px;
    line-height: 1;
  }
  .contact {
    position: absolute;
    left: 476px;
    top: 62px;
    color: var(--white);
  }
  .contact__name {
    color: var(--gold-deep);
    font-size: 21px;
    font-weight: 700;
    line-height: 1.2;
  }
  .contact__role {
    color: var(--gold-deep);
    font-size: 21px;
    line-height: 1.2;
    margin-bottom: 18px;
  }
  .contact__line {
    font-size: 19px;
    line-height: 30px;
  }
  .contact__line b { font-weight: 700; }
  .contact__line--gap { margin-top: 6px; }
  .address {
    position: absolute;
    left: 40px;
    top: 410px;
    color: var(--white);
    font-size: 20px;
  }
</style>
</head>
<body>
<main class="canvas">
  <section class="card card--front" aria-label="Business card front">
    <svg class="card__wave" viewBox="0 0 798 457" aria-hidden="true">
      <path class="wave-band" d="M0,372 C60,345 120,327 168,326 C320,350 450,410 570,411 C680,411 752,374 798,348 L798,457 L0,457 Z" fill="var(--maroon)"/>
      <path class="wave-swoosh" d="M168,324 C330,326 450,392 570,394 C680,396 750,352 798,322 L798,339 C752,368 680,404 570,404 C450,402 320,346 168,324 Z" fill="var(--gold)"/>
    </svg>
    <div class="wordmark wordmark--front">Marlow &amp; Quince</div>
    <div class="contact">
      <p class="contact__name">Your Name</p>
      <p class="contact__role">Designation</p>
      <p class="contact__line"><b>p</b> : 123-456-7890</p>
      <p class="contact__line"><b>c</b> : 123-456-7890</p>
      <p class="contact__line"><b>f</b> : 123-456-7890</p>
      <p class="contact__line contact__line--gap"><b>e</b> : name@yourwebsite.com</p>
      <p class="contact__line"><b>w</b> : www.marlowquince.com</p>
    </div>
    <p class="address">0000, Street Name, City Name, Country Code.</p>
  </section>

  <section class="card card--back" aria-label="Business card back">
    <div class="wordmark wordmark--back">M &amp; Q</div>
  </section>
</main>
</body>
</html>
```